Dental Business Card Design w/logo

Classic, elegant w/a touch of contemporary
Upscale dental facility located in Modesto CA
Specializing in restorative & general dentistry
Providing exceptional customer service to the community
Updates

I prefer script and not bold writing
If you can use the phone; fax and email icons instead of spelling them out, it would be great
No bold colors
Classy and elegant
In the back of the card I would like to see something like this
Your Next Appointment:
Mon     Tue    Wed    Thur (a box next to each of them for marking)
Date:_______________ at_____________ AM    PM  (a box next to them for marking)

Thank you

Target Market(s)

Well established professional

Industry/Entity Type

Dental

Contact Information for Business Card

Velarina Tossudi DMD
4176 Marlow Rd
Suite K7
Modesto, CA 95418

Office: 209-731-5920
Fax: 209-731-8047
Email: tossudidmd@quillmail.example

Requirements
Must have
• Unique classic logo
An easily repeatable design that can be used on letterhead and envelopes
Nice to have
• My initials incorporated into unique design
Should not have
• No cartoons or cheesy themes. This is a practice for the well established and professional individual.

```html
<!DOCTYPE html>
<html lang="en">
<head>
<meta charset="utf-8">
<title>Velarina Tossudi, D.M.D. — Stationery</title>
<link rel="stylesheet" href="https://fonts.googleapis.com/css2?family=EB+Garamond:ital,wght@0,400;1,400&display=swap">
<style>
  :root {
    --backdrop: #2a2a2a;
    --paper: #ffffff;
    --paper-shade: #f3f3f3;
    --ink: #7a7a7a;
    --ink-soft: #9a9a9a;
    --accent: #8fd0d0;
    --rule: #bdbdbd;
  }
  * { box-sizing: border-box; margin: 0; padding: 0; }
  html, body { width: 1200px; height: 970px; overflow: hidden; }
  body {
    background: var(--backdrop);
    font-family: "EB Garamond", Georgia, serif;
    color: var(--ink);
    position: relative;
  }
  .sheet {
    position: absolute;
    background: linear-gradient(180deg, var(--paper) 0%, var(--paper-shade) 100%);
  }

  /* Brand mark: name set in text with a plain circle */
  .brand-mark { display: flex; align-items: center; gap: 8px; color: var(--accent); }
  .brand-mark__dot { width: 14px; height: 14px; border-radius: 50%; background: var(--accent); flex: none; }
  .brand-mark__name { font-size: 17px; letter-spacing: 0.04em; white-space: nowrap; }

  .practice-name { text-transform: uppercase; letter-spacing: 0.06em; color: var(--ink); }
  .practice-tagline { font-style: italic; color: var(--ink-soft); }
  .label { color: var(--accent); }
  .email { color: var(--accent); }

  /* Letterhead */
  .letterhead { left: 113px; top: 75px; width: 584px; height: 825px; }
  .letterhead__header { position: absolute; top: 38px; left: 0; right: 0; display: flex; flex-direction: column; align-items: center; }
  .letterhead__header .brand-mark { margin-bottom: 22px; }
  .letterhead__header .practice-name { font-size: 10px; }
  .letterhead__header .practice-tagline { font-size: 9px; margin-top: 1px; }
  .letterhead__footer { position: absolute; bottom: 28px; left: 0; right: 0; text-align: center; font-size: 7.5px; line-height: 1.25; letter-spacing: 0.05em; }
  .letterhead__footer .email { margin-top: 6px; display: block; }

  /* Envelope */
  .envelope { left: 463px; top: 484px; width: 608px; height: 302px; box-shadow: 0 0 0 1px #e2e2e2; }
  .envelope__return { position: absolute; top: 16px; left: 14px; display: flex; align-items: flex-start; gap: 14px; }
  .envelope__return .brand-mark { padding-top: 8px; }
  .envelope__text .practice-name { font-size: 12px; }
  .envelope__text .practice-tagline { font-size: 11.5px; }
  .envelope__text .address { font-size: 9px; letter-spacing: 0.06em; margin-top: 2px; }

  /* Business cards */
  .card { width: 150px; height: 252px; top: 94px; text-align: center; }
  .card--front { left: 748px; }
  .card--front .brand-mark { position: absolute; top: 38px; left: 0; right: 0; justify-content: center; gap: 5px; }
  .card--front .brand-mark__name { font-size: 11px; }
  .card--front .brand-mark__dot { width: 9px; height: 9px; }
  .card__identity { position: absolute; top: 110px; left: 0; right: 0; }
  .card__identity .practice-name { font-size: 7px; }
  .card__identity .practice-tagline { font-size: 6px; }
  .card__contact { position: absolute; top: 182px; left: 0; right: 0; font-size: 5.5px; line-height: 1.3; letter-spacing: 0.05em; }
  .card__contact .phones { margin-top: 8px; }
  .card__contact .email { margin-top: 6px; display: block; }

  .card--back { left: 918px; text-align: left; padding: 0 12px; }
  .appointment__title { margin-top: 70px; text-align: center; font-size: 7.5px; color: var(--ink); letter-spacing: 0.04em; }
  .appointment__days { display: flex; justify-content: space-between; margin-top: 14px; font-size: 5.5px; font-style: italic; }
  .checkbox { display: inline-block; width: 4px; height: 4px; border: 0.6px solid var(--ink); margin-right: 2px; vertical-align: middle; }
  .appointment__line { display: flex; align-items: flex-end; gap: 3px; margin-top: 12px; font-size: 5.5px; font-style: italic; }
  .fill { flex: 1; border-bottom: 0.6px solid var(--rule); height: 5px; }
  .fill--short { flex: 0 0 40px; }
  .appointment__note { position: absolute; bottom: 26px; left: 18px; right: 18px; text-align: center; font-size: 5px; font-style: italic; line-height: 1.35; color: var(--ink-soft); }
</style>
</head>
<body>

  <section class="sheet letterhead" aria-label="Letterhead">
    <header class="letterhead__header">
      <div class="brand-mark"><span class="brand-mark__dot"></span><span class="brand-mark__name">Velarina Tossudi</span></div>
      <p class="practice-name">Velarina Tossudi, D.M.D.</p>
      <p class="practice-tagline">General &amp; Restorative Dentistry</p>
    </header>
    <footer class="letterhead__footer">
      <p>4176 Marlow Rd. Suite K7</p>
      <p>Modesto, CA 95418</p>
      <p><span class="label">T:</span> 209 731 5920 &nbsp;<span class="label">F:</span> 209 731 8047</p>
      <span class="email">tossudidmd@quillmail.example</span>
    </footer>
  </section>

  <section class="sheet card card--front" aria-label="Business card front">
    <div class="brand-mark"><span class="brand-mark__dot"></span><span class="brand-mark__name">Velarina Tossudi</span></div>
    <div class="card__identity">
      <p class="practice-name">Velarina Tossudi, D.M.D.</p>
      <p class="practice-tagline">General &amp; Restorative Dentistry</p>
    </div>
    <div class="card__contact">
      <p>4176 Marlow Rd. Suite K7</p>
      <p>Modesto, CA 95418</p>
      <div class="phones">
        <p><span class="label">T:</span> 209 731 5920</p>
        <p><span class="label">F:</span> 209 731 8047</p>
      </div>
      <span class="email">tossudidmd@quillmail.example</span>
    </div>
  </section>

  <section class="sheet card card--back" aria-label="Business card back">
    <p class="appointment__title">Your Next Appointment:</p>
    <div class="appointment__days">
      <span><span class="checkbox"></span>Mon.</span>
      <span><span class="checkbox"></span>Tue.</span>
      <span><span class="checkbox"></span>Wed.</span>
      <span><span class="checkbox"></span>Thur.</span>
      <span><span class="checkbox"></span>Fri.</span>
    </div>
    <div class="appointment__line"><span>Date:</span><span class="fill"></span></div>
    <div class="appointment__line"><span>Time:</span><span class="fill fill--short"></span><span><span class="checkbox"></span>am</span><span><span class="checkbox"></span>pm</span></div>
    <p class="appointment__note">If unable to keep this appointment, kindly give 48 hours notice, otherwise a charge will be made for time reserved.</p>
  </section>

  <section class="sheet envelope" aria-label="Envelope">
    <div class="envelope__return">
      <div class="brand-mark"><span class="brand-mark__dot"></span></div>
      <div class="envelope__text">
        <p class="practice-name">Velarina Tossudi, D.M.D.</p>
        <p class="practice-tagline">General &amp; Restorative Dentistry</p>
        <p class="address">4176 Marlow Rd. Suite K7 Modesto, CA 95418</p>
      </div>
    </div>
  </section>

</body>
</html>
```